Redesign of luchtvoorraadpunt.nl – Clean, Trustworthy & User-Friendly Medical Equipment We...

PLEASE DO NOT CONTACT US OUTSIDE KRAVELPOINT.COM

We are looking for a talented and creative web designer to redesign the website www.luchtvoorraadpunt.nl, a Dutch online store specializing in medical oxygen concentrators and related products.

The current website is functional but outdated in terms of design, structure, and user experience. We want a fresh, modern, and trustworthy design that reflects the medical and professional nature of the business, while also being clear, accessible, and easy to navigate for a broad audience — including elderly users and people with limited technical skills.

About the Business:
Luchtvoorraadpunt.nl provides high-quality oxygen concentrators and accessories for both home and mobile use. The target audience includes individuals with respiratory conditions, healthcare professionals, and caregivers. Trust, clarity, and ease of use are key.

What We’re Looking For:
A clean and modern layout with a medical/professional feel
Strong focus on usability and accessibility
A design that works flawlessly on desktop and mobile (responsive)
Clear product presentation and easy-to-use navigation
Use of calming colors (e.g. white, light blue, grey tones) that reflect a medical/healthcare environment
Clear call-to-actions (e.g. “Vraag een offerte aan”, “Neem contact op”, etc.)
A design that builds trust and encourages inquiries or purchases

Pages We Need Designed:
Homepage
Product overview page (category)
Product detail page

Inspiration / Style Examples:
We’re looking for something in the style of:

Varnoth Healthcare
Bralto.nl
Welzijnsdepot.nl
Quenby (for clean layout and spacing)

Deliverables:
Full desktop and mobile designs (Figma, Adobe PS)
All source files and assets used (fonts, icons, images, etc.)
Clean and organized layers
Design must be ready for implementation by our development team

Target Market(s)

Luchtvoorraadpunt.nl targets both B2C and B2B audiences within the medical and healthcare sector in europe

Industry/Entity Type

Medical

Number of Pages Required

2 page

Font styles to use
Sans Serif

Requirements
Must have
• Clean and professional design, responsive layout (desktop and mobile), calming medical color scheme (e.g. light blue, white, grey), clear product presentation with specs and images, strong call-to-actions (e.g. "Vraag een offerte aan"), trust elements (certifications, reviews, support info), easy navigation for elderly and non-tech-savvy users, contact form easily accessible, SEO-friendly structure, fast loading design, privacy and regulatory compliance elements (e.g. CE mark info, medical disclaimers).
Should not have
• Overly complex design, dark or aggressive color schemes, small or hard-to-read fonts, cluttered layout, distracting animations, unnecessary pop-ups, autoplay videos or sounds, technical jargon without explanation, hidden contact options, slow-loading pages.

```html
<!DOCTYPE html>
<html lang="en">
<head>
<meta charset="utf-8">
<title>Luchtvoorraadpunt.nl – Home</title>
<link href="https://fonts.googleapis.com/css2?family=Roboto:wght@400;500;700;900&display=swap" rel="stylesheet">
<style>
:root{
  --blue:#1d9bf0;
  --blue-dark:#1583d1;
  --ink:#1b1b1b;
  --text:#444;
  --muted:#777;
  --line:#e3e6ea;
  --soft:#f4f6f8;
  --panel:#f1f2f4;
  --footer:#3b3b3b;
  --footer-bottom:#2c2c2c;
  --white:#fff;
}
*{box-sizing:border-box;margin:0;padding:0}
html,body{width:1200px;height:5115px;overflow:hidden}
body{font-family:'Roboto',sans-serif;color:var(--ink);background:var(--white);position:relative}
.abs{position:absolute}
a{color:inherit;text-decoration:none}

/* top bar */
.topbar{position:absolute;left:0;top:0;width:1200px;height:32px;background:var(--blue);color:#fff;font-size:11px}
.topbar .left{position:absolute;left:131px;top:0;height:32px;display:flex;align-items:center;gap:10px}
.topbar .right{position:absolute;right:131px;top:0;height:32px;display:flex;align-items:center;gap:10px}
.topbar .sep{opacity:.6}
.flag{width:20px;height:12px;background:#fff;border-radius:2px;display:inline-block;vertical-align:middle;margin-right:4px}

/* header */
.header{position:absolute;left:0;top:32px;width:1200px;height:48px;background:#fff}
.brand{position:absolute;left:131px;top:6px;display:flex;align-items:center;gap:6px;font-weight:900;font-size:30px;color:var(--blue);letter-spacing:-.5px}
.brand .dot{width:12px;height:12px;border-radius:50%;background:var(--blue)}
.search{position:absolute;left:618px;top:12px;width:276px;height:26px;border:1px solid #cfd6dd;border-radius:14px;display:flex;align-items:center;overflow:hidden;font-size:10px}
.search .all{background:var(--blue);color:#fff;height:100%;padding:0 10px;display:flex;align-items:center;font-weight:500}
.search .ph{color:#999;padding-left:8px;flex:1}
.search svg{margin-right:10px}
.cart{position:absolute;left:904px;top:19px;font-size:10px;font-weight:500;display:flex;align-items:center;gap:10px}
.menu-btn{position:absolute;left:1038px;top:12px;width:26px;height:26px;border-radius:50%;background:#e6e8eb;display:flex;align-items:center;justify-content:center}

/* hero */
.hero{position:absolute;left:0;top:80px;width:1200px;height:433px;background:linear-gradient(110deg,#cfc6b8 0%,#a89e90 35%,#b9b2a7 60%,#8d8579 100%)}
.hero h1{position:absolute;left:0;width:1200px;top:118px;text-align:center;color:#fff;font-size:36px;font-weight:700}
.hero p{position:absolute;left:0;width:1200px;top:180px;text-align:center;color:#fff;font-size:22px;font-weight:400}
.hero .btns{position:absolute;left:0;width:1200px;top:294px;display:flex;justify-content:center;gap:22px}
.btn{display:inline-flex;align-items:center;justify-content:center;border-radius:22px;font-weight:700;font-size:12px;letter-spacing:.3px}
.hero .btn{width:178px;height:40px}
.btn-blue{background:var(--blue);color:#fff}
.btn-white{background:#fff;color:var(--ink)}
.hero-arrow{position:absolute;top:187px;width:42px;height:42px;border-radius:50%;display:flex;align-items:center;justify-content:center}
.hero-arrow.l{left:128px;background:#333}
.hero-arrow.r{left:1028px;background:#fff}

/* about */
.down-circle{position:absolute;left:570px;top:560px;width:60px;height:60px;border:2px solid #333;border-radius:50%;display:flex;align-items:center;justify-content:center}
.about h2{position:absolute;left:0;width:1200px;top:656px;text-align:center;font-size:20px;font-weight:700}
.about .copy{position:absolute;left:250px;width:700px;top:706px;text-align:center;font-size:13.5px;line-height:23px;color:var(--text)}
.about .copy p+p{margin-top:22px}

/* section heads */
.eyebrow{position:absolute;left:133px;font-size:16px;color:var(--text)}
.sec-title{position:absolute;left:133px;font-size:22px;font-weight:700}
.view-all{position:absolute;font-size:16px;color:var(--text);text-decoration:underline;display:flex;align-items:center;gap:8px}

/* categories */
.cat{position:absolute;width:296px}
.cat .img{width:296px;height:173px;border-radius:4px}
.cat h3{margin-top:16px;font-size:19px;font-weight:700}
.cat p{margin-top:10px;font-size:13.5px;line-height:24px;color:var(--text);width:240px}
.cat .go{position:absolute;right:0;top:196px;width:42px;height:42px;border-radius:50%;background:var(--blue);display:flex;align-items:center;justify-content:center}

/* products band */
.products-band{position:absolute;left:0;top:1722px;width:1200px;height:594px;background:var(--soft)}
.products-band .inner{position:absolute;left:68px;top:0;width:1064px;height:10px;background:#fff}
.tabs{position:absolute;left:133px;top:1890px;display:flex;font-size:14px;color:var(--ink)}
.tabs span{padding:0 18px;border-left:1px solid #ccc;line-height:16px}
.tabs span:first-child{padding-left:0;border-left:none;color:var(--blue);text-decoration:underline}
.pcard{position:absolute;width:209px;height:283px;background:#fff;border-radius:6px;box-shadow:0 2px 8px rgba(0,0,0,.12);padding:12px 12px 0}
.pcard .pimg{height:128px;margin:0 30px;border-radius:4px}
.pcard .bl{margin-top:12px;font-size:10px;color:var(--blue);text-decoration:underline}
.pcard .nm{margin-top:6px;font-size:15px;font-weight:700}
.pcard .lbl{position:absolute;left:12px;top:230px;font-size:9px;font-weight:700}
.pcard .brs{position:absolute;left:12px;top:246px;font-size:8.5px;color:var(--muted);white-space:nowrap}
.car-arrow{position:absolute;width:42px;height:42px;border-radius:50%;background:#666;display:flex;align-items:center;justify-content:center}

/* mission */
.mission{position:absolute;left:171px;top:2316px;width:857px;height:477px;background:linear-gradient(90deg,#1d1d1f 0%,#2b2a2a 40%,#6e6862 75%,#8b8680 100%)}
.mission .eb{position:absolute;left:64px;top:66px;color:#ddd;font-size:12px}
.mission h2{position:absolute;left:64px;top:102px;color:#fff;font-size:26px;font-weight:700;line-height:37px}
.mission .txt{position:absolute;left:64px;top:196px;width:400px;color:#fff;font-size:16.5px;line-height:28px;text-align:justify}
.feat{position:absolute;width:127px;height:153px;background:var(--blue);border-radius:4px;color:#fff;text-align:center;padding-top:10px}
.feat .ic{width:36px;height:36px;border-radius:50%;background:#fff;margin:0 auto;display:flex;align-items:center;justify-content:center}
.feat h4{margin-top:8px;font-size:14px;font-weight:700;line-height:17px}
.feat p{margin-top:6px;font-size:10.5px;line-height:17px;opacity:.9;padding:0 10px}

/* gallery */
.gcard{position:absolute;width:290px;height:178px;background:#fff;border-radius:6px;box-shadow:0 2px 8px rgba(0,0,0,.13);overflow:hidden}
.gcard .plus{position:absolute;left:28px;top:70px;width:36px;height:36px;border-radius:50%;background:var(--blue);display:flex;align-items:center;justify-content:center}
.gcard .vw{position:absolute;left:24px;top:122px;font-size:17px}
.gcard .gimg{position:absolute;right:14px;top:10px;width:130px;height:158px;border-radius:4px}
.dots{position:absolute;display:flex;gap:16px}
.dots i{width:12px;height:12px;border-radius:50%;background:#aaa;display:block}
.dots i:first-child{background:var(--blue)}

/* contact */
.contact{position:absolute;left:133px;top:3469px;width:934px;height:486px;background:var(--panel)}
.contact .eb{position:absolute;left:24px;top:64px;font-size:16px;color:var(--text)}
.contact h2{position:absolute;left:24px;top:96px;font-size:22px;font-weight:700}
.crow{position:absolute;left:24px;width:594px;height:60px;display:flex;align-items:center}
.crow .t{flex:1;margin-left:12px;font-size:16px;font-weight:700}
.crow .btn{width:183px;height:38px;font-size:11px}
.btn-outline{border:2px solid #222;color:#222}
.btn-outline-blue{border:2px solid var(--blue);color:var(--blue)}
.contact .hr{position:absolute;left:24px;width:594px;height:1px;background:#d4d7db}
.contact .photo{position:absolute;right:0;top:0;width:272px;height:486px;background:linear-gradient(160deg,#e9edf1,#c9d1d9 55%,#8f9aa6)}

/* brands */
.brandbox{position:absolute;top:4123px;width:94px;height:89px;border:1px solid var(--line);border-radius:4px;display:flex;align-items:center;justify-content:center;font-size:14px;font-weight:500;color:#6a6a6a;text-align:center;line-height:16px}

/* footer */
.footer{position:absolute;left:0;top:4785px;width:1200px;height:330px;background:var(--footer);color:#ddd}
.footer .col{position:absolute;top:86px}
.footer h5{font-size:13px;font-weight:700;color:#fff;letter-spacing:.3px}
.footer ul{list-style:none;margin-top:30px;font-size:12px;line-height:23px;color:#d0d0d0}
.footer .bottom{position:absolute;left:0;bottom:0;width:1200px;height:52px;background:var(--footer-bottom);display:flex;align-items:center;justify-content:center;font-size:10.5px;color:#ccc}
.video-btn{position:absolute;left:564px;top:4752px;width:72px;height:72px;border-radius:50%;background:var(--blue);display:flex;align-items:center;justify-content:center;color:#fff;font-size:11px;font-weight:700}
.up-btn{position:absolute;left:1008px;top:4933px;width:58px;height:58px;border-radius:50%;background:var(--blue);display:flex;align-items:center;justify-content:center}
</style>
</head>
<body>

<!-- top bar -->
<div class="topbar">
  <div class="left">
    <svg width="16" height="16" viewBox="0 0 16 16"><circle cx="8" cy="8" r="8" fill="#fff"/><path d="M5.5 4.5l1.5 0 .7 2-1 .7a5 5 0 0 0 2.2 2.2l.7-1 2 .7v1.5c0 .5-.4.9-.9.9A6.7 6.7 0 0 1 4.6 5.4c0-.5.4-.9.9-.9z" fill="var(--blue)"/></svg>
    <span>0031-701234567</span><span class="sep">|</span><span>About Us</span><span class="sep">|</span><span>Contact Us</span>
  </div>
  <div class="right">
    <span><i class="flag"></i>English ▾</span><span class="sep">|</span>
    <span>Delivery</span>
    <svg width="20" height="14" viewBox="0 0 20 14"><rect x="1" y="2" width="11" height="8" fill="none" stroke="#fff"/><path d="M12 5h4l3 3v2h-7z" fill="none" stroke="#fff"/><circle cx="5" cy="12" r="1.5" fill="#fff"/><circle cx="15" cy="12" r="1.5" fill="#fff"/></svg>
    <span class="sep">|</span><span>Stock</span>
    <svg width="16" height="14" viewBox="0 0 16 14"><rect x="1" y="1" width="14" height="12" fill="none" stroke="#fff"/><path d="M1 5h14" stroke="#fff"/></svg>
    <span class="sep">|</span><span>Compare</span>
    <svg width="16" height="14" viewBox="0 0 16 14"><path d="M2 4h11l-3-3M14 10H3l3 3" fill="none" stroke="#fff" stroke-width="1.3"/></svg>
    <span class="sep">|</span><span>Wishlist</span>
    <svg width="16" height="14" viewBox="0 0 16 14"><path d="M8 13S1 8.5 1 4.5A3.3 3.3 0 0 1 8 3a3.3 3.3 0 0 1 7 1.5C15 8.5 8 13 8 13z" fill="none" stroke="#fff" stroke-width="1.3"/></svg>
    <span class="sep">|</span>
    <svg width="22" height="22" viewBox="0 0 22 22"><circle cx="11" cy="11" r="10" fill="none" stroke="#fff" stroke-width="1.5"/><circle cx="11" cy="9" r="3.5" fill="#fff"/><path d="M5 17a7 7 0 0 1 12 0" fill="#fff"/></svg>
  </div>
</div>

<!-- header -->
<header class="header">
  <div class="brand"><span class="dot"></span>aerivo</div>
  <div class="search">
    <span class="all">All ▾</span><span class="ph">What are you looking for?</span>
    <svg width="14" height="14" viewBox="0 0 14 14"><circle cx="6" cy="6" r="4.5" fill="none" stroke="#555" stroke-width="1.4"/><path d="M9.5 9.5l3.5 3.5" stroke="#555" stroke-width="1.4"/></svg>
  </div>
  <div class="cart">0 item(s) - €0.00
    <svg width="22" height="18" viewBox="0 0 22 18"><path d="M1 1h3l2.5 11h11l2-8H5.5" fill="none" stroke="#333" stroke-width="1.5"/><circle cx="8" cy="15.5" r="1.5" fill="#333"/><circle cx="16" cy="15.5" r="1.5" fill="#333"/></svg>
  </div>
  <div class="menu-btn"><svg width="12" height="10" viewBox="0 0 12 10"><path d="M0 1h12M0 5h12M0 9h12" stroke="#333" stroke-width="1.5"/></svg></div>
</header>

<!-- hero -->
<section class="hero" role="img" aria-label="Smiling older man seated in a bright living room next to a home oxygen concentrator">
  <h1>NORDAIR ECLIPTA 5</h1>
  <p>The most affordable oxygen concentrator</p>
  <div class="btns"><a class="btn btn-blue">REQUEST A QUOTE</a><a class="btn btn-white">GET IN TOUCH</a></div>
  <div class="hero-arrow l"><svg width="16" height="14" viewBox="0 0 16 14"><path d="M15 7H2M7 1L1 7l6 6" fill="none" stroke="#fff" stroke-width="1.8"/></svg></div>
  <div class="hero-arrow r"><svg width="16" height="14" viewBox="0 0 16 14"><path d="M1 7h13M9 1l6 6-6 6" fill="none" stroke="#333" stroke-width="1.8"/></svg></div>
</section>

<!-- about -->
<section class="about">
  <div class="down-circle"><svg width="16" height="24" viewBox="0 0 16 24"><path d="M8 1v21M1 15l7 7 7-7" fill="none" stroke="#333" stroke-width="1.8"/></svg></div>
  <h2>WHO WE ARE AND WHAT WE DO?</h2>
  <div class="copy">
    <p>As business and consumer you want the best equipment for the sharpest prices. We offer the best stationary oxygen concentrators, portable oxygen concentrators, accessories and disposables. Compare and make the best choice for you and your business.</p>
    <p>Aerivo BV more than 22 years experience your partner for innovative technology and service. With our online shop we keep you constantly informed of the various systems. Questons or wishes? don't hesitate to contact us</p>
  </div>
</section>

<!-- categories -->
<div class="eyebrow" style="top:945px">Our all featured categories</div>
<h2 class="sec-title" style="top:978px">ALL AEROSPLITTER CATEGORIES</h2>
<a class="view-all" style="left:896px;top:980px">View all category <svg width="16" height="12" viewBox="0 0 16 12"><path d="M1 6h13M9 1l5 5-5 5" fill="none" stroke="#444" stroke-width="1.5"/></svg></a>

<div class="cat" style="left:131px;top:1035px">
  <div class="img" role="img" aria-label="Home oxygen concentrator on a side table by a window" style="background:linear-gradient(135deg,#8f7a64,#d9d4cc 55%,#6f5a46)"></div>
  <h3>Oxygen Concentrator</h3><p>An oxygen concentrator is a medical device designed to deliver a continuous and reliable...</p>
  <div class="go"><svg width="16" height="14" viewBox="0 0 16 14"><path d="M1 7h13M9 1l6 6-6 6" fill="none" stroke="#fff" stroke-width="1.8"/></svg></div>
</div>
<div class="cat" style="left:453px;top:1035px">
  <div class="img" role="img" aria-label="Patient resting with an oxygen mask" style="background:linear-gradient(135deg,#7c8f9e,#d7dde2 55%,#a7b3bd)"></div>
  <h3>Supplies</h3><p>Our Oxygen Concentrator Supplies ensure that every user receives safe, uninterrupted,and...</p>
  <div class="go"><svg width="16" height="14" viewBox="0 0 16 14"><path d="M1 7h13M9 1l6 6-6 6" fill="none" stroke="#fff" stroke-width="1.8"/></svg></div>
</div>
<div class="cat" style="left:773px;top:1035px">
  <div class="img" role="img" aria-label="Man seated beside a portable oxygen concentrator" style="background:linear-gradient(135deg,#e3e3e1,#bdb8b0 55%,#5d5a57)"></div>
  <h3>Aerivo Portable Concentrator</h3><p>A Portable Oxygen Concentrator (POC) is a lightweight, compact medical device designed to ...</p>
  <div class="go"><svg width="16" height="14" viewBox="0 0 16 14"><path d="M1 7h13M9 1l6 6-6 6" fill="none" stroke="#fff" stroke-width="1.8"/></svg></div>
</div>
<div class="cat" style="left:131px;top:1385px">
  <div class="img" role="img" aria-label="Older woman using a nasal oxygen cannula" style="background:linear-gradient(135deg,#5f7f5a,#c9c2b8 55%,#8a8479)"></div>
  <h3>Oxygen Filter</h3><p>An oxygen concentrator is a medical device designed to deliver a continuous and reliable...</p>
  <div class="go"><svg width="16" height="14" viewBox="0 0 16 14"><path d="M1 7h13M9 1l6 6-6 6" fill="none" stroke="#fff" stroke-width="1.8"/></svg></div>
</div>
<div class="cat" style="left:453px;top:1385px">
  <div class="img" role="img" aria-label="Rows of blue oxygen cylinders at a filling station" style="background:linear-gradient(135deg,#0e5f95,#2aa3dc 50%,#0b4a78)"></div>
  <h3>Oxygen Filling Station</h3><p>An Oxygen Filling Station is a specialized facility designed for the safe production, storage, and ...</p>
  <div class="go"><svg width="16" height="14" viewBox="0 0 16 14"><path d="M1 7h13M9 1l6 6-6 6" fill="none" stroke="#fff" stroke-width="1.8"/></svg></div>
</div>
<div class="cat" style="left:773px;top:1385px">
  <div class="img" role="img" aria-label="Oxygen cylinders fitted with flow regulators" style="background:linear-gradient(135deg,#f2f2f0,#cfd3cf 55%,#7fae7a)"></div>
  <h3>AeroSplitter</h3><p>AeroSplitter is a high-performance oxygen optimization and distribution system designed to enhance</p>
  <div class="go"><svg width="16" height="14" viewBox="0 0 16 14"><path d="M1 7h13M9 1l6 6-6 6" fill="none" stroke="#fff" stroke-width="1.8"/></svg></div>
</div>

<!-- products -->
<div class="products-band"><div class="inner"></div></div>
<div class="eyebrow" style="top:1797px">Our all featured products</div>
<h2 class="sec-title" style="top:1831px">ALL AERIVO PRODUCTS</h2>
<div class="tabs"><span>All Products</span><span>Oxygen Concentrator</span><span>Portable Oxygen Concentrator</span><span>Filters</span><span>Supplies</span></div>

<div class="pcard" style="left:-108px;top:1945px"><div class="pimg" role="img" aria-label="Blue home oxygen concentrator" style="background:linear-gradient(90deg,#2f7fc9,#5fa8e6)"></div><div class="bl">Pulmatek</div><div class="nm">Lumen 5 Pro</div><div class="lbl">BRANDS</div><div class="brs">Varnoth | Torvell Labs Inc</div></div>
<div class="pcard" style="left:133px;top:1945px"><div class="pimg" role="img" aria-label="Blue stationary oxygen concentrator" style="background:linear-gradient(90deg,#3b8fd6,#7bb9ea)"></div><div class="bl">Varnoth Healthcare</div><div class="nm">Varnoth Calmflo</div><div class="lbl">BRANDS</div><div class="brs">AERIVO BV &nbsp;|&nbsp; Varnoth Healthcare &nbsp;|&nbsp; Torvell Labs Inc</div></div>
<div class="pcard" style="left:374px;top:1945px"><div class="pimg" role="img" aria-label="Grey and black oxygen concentrator" style="background:linear-gradient(90deg,#9a9a9a,#dcdcdc 50%,#3a3a3a)"></div><div class="bl">Varnoth Healthcare</div><div class="nm">Varnoth Airmate</div><div class="lbl">BRANDS</div><div class="brs">Varnoth Healthcare &nbsp;|&nbsp; Torvell Labs Inc</div></div>
<div class="pcard" style="left:616px;top:1945px"><div class="pimg" role="img" aria-label="White portable oxygen concentrator" style="background:linear-gradient(90deg,#e8eef3,#c5d3de)"></div><div class="bl">Brevix</div><div class="nm">Brevix Roam 6</div><div class="lbl">BRANDS</div><div class="brs">Brevix</div></div>
<div class="pcard" style="left:856px;top:1945px"><div class="pimg" role="img" aria-label="White and blue compact oxygen concentrator" style="background:linear-gradient(90deg,#dfe9f2,#9fbedb)"></div><div class="bl">Pulmatek</div><div class="nm">Lumen 5</div><div class="lbl">BRANDS</div><div class="brs">Pulmatek</div></div>
<div class="pcard" style="left:1097px;top:1945px"><div class="pimg" role="img" aria-label="White and blue compact oxygen concentrator" style="background:linear-gradient(90deg,#dfe9f2,#9fbedb)"></div><div class="bl">Pulmatek</div><div class="nm">Lumen 5</div><div class="lbl">BRANDS</div><div class="brs">Pulmatek</div></div>
<div class="car-arrow" style="left:102px;top:2064px"><svg width="14" height="14" viewBox="0 0 14 14"><path d="M9 2L4 7l5 5" fill="none" stroke="#fff" stroke-width="1.8"/></svg></div>
<div class="car-arrow" style="left:1052px;top:2064px"><svg width="14" height="14" viewBox="0 0 14 14"><path d="M5 2l5 5-5 5" fill="none" stroke="#fff" stroke-width="1.8"/></svg></div>

<!-- mission -->
<section class="mission" role="img" aria-label="Smiling older couple at home, dark toned backdrop">
  <div class="eb">Our Mission &amp; Vision</div>
  <h2>AERIVO BV OXYGEN<br>CONCENTRATOR</h2>
  <div class="txt">AERIVO BV was founded in 2003 and has a premium range of oxygen concentrators. We have the largest online offers for the Netherlands and Belgium.Whether you are looking for a fixed oxygen concentrator or a portable / mobile oxygen concentrator. We make the difference in knowledge, service and low prices.</div>
</section>
<div class="feat" style="left:682px;top:2384px"><div class="ic"><svg width="20" height="16" viewBox="0 0 20 14"><rect x="1" y="2" width="11" height="8" fill="none" stroke="#1d9bf0" stroke-width="1.4"/><path d="M12 5h4l3 3v2h-7z" fill="none" stroke="#1d9bf0" stroke-width="1.4"/></svg></div><h4>Free<br>Shipping</h4><p>above € 250 in the EU</p></div>
<div class="feat" style="left:843px;top:2384px"><div class="ic"><svg width="16" height="20" viewBox="0 0 16 20"><rect x="3" y="1" width="10" height="18" rx="2" fill="none" stroke="#1d9bf0" stroke-width="1.4"/><circle cx="8" cy="8" r="2.5" fill="#1d9bf0"/></svg></div><h4>Oxygen<br>Concentrator</h4><p>Oxygen concentrator for travel</p></div>
<div class="feat" style="left:682px;top:2573px"><div class="ic"><svg width="18" height="18" viewBox="0 0 18 18"><path d="M3 6h12l-1 10H4z" fill="none" stroke="#1d9bf0" stroke-width="1.4"/><path d="M6 6a3 3 0 0 1 6 0" fill="none" stroke="#1d9bf0" stroke-width="1.4"/></svg></div><h4>Secure<br>Shopping</h4><p>Best security features</p></div>
<div class="feat" style="left:843px;top:2573px"><div class="ic"><svg width="18" height="18" viewBox="0 0 18 18"><circle cx="9" cy="7" r="5" fill="none" stroke="#1d9bf0" stroke-width="1.4"/><path d="M6 11l-2 6 5-2 5 2-2-6" fill="none" stroke="#1d9bf0" stroke-width="1.4"/></svg></div><h4>22 years<br>experience</h4><p>we deliver reliable and results</p></div>

<!-- gallery -->
<div class="eyebrow" style="top:2882px">Our Gallery</div>
<h2 class="sec-title" style="top:2916px">GALLERY HOME PAGE</h2>

<div class="gcard" style="left:-187px;top:2981px"><div class="gimg" role="img" aria-label="Blue and white oxygen concentrator" style="background:linear-gradient(90deg,#2c6fbd,#e8eef4)"></div></div>
<div class="gcard" style="left:133px;top:2981px"><div class="plus"><svg width="14" height="14" viewBox="0 0 14 14"><path d="M7 1v12M1 7h12" stroke="#fff" stroke-width="2"/></svg></div><div class="vw">View</div><div class="gimg" role="img" aria-label="Blue and white oxygen concentrator" style="background:linear-gradient(90deg,#e8eef4,#2c6fbd)"></div></div>
<div class="gcard" style="left:455px;top:2981px"><div class="plus"><svg width="14" height="14" viewBox="0 0 14 14"><path d="M7 1v12M1 7h12" stroke="#fff" stroke-width="2"/></svg></div><div class="vw">View</div><div class="gimg" role="img" aria-label="Black stationary oxygen concentrator" style="background:linear-gradient(90deg,#555,#1c1c1c)"></div></div>
<div class="gcard" style="left:775px;top:2981px"><div class="plus"><svg width="14" height="14" viewBox="0 0 14 14"><path d="M7 1v12M1 7h12" stroke="#fff" stroke-width="2"/></svg></div><div class="vw">View</div><div class="gimg" role="img" aria-label="Light blue oxygen concentrator" style="background:linear-gradient(90deg,#a8cdee,#3d8fd6)"></div></div>
<div class="gcard" style="left:1095px;top:2981px"><div class="plus"><svg width="14" height="14" viewBox="0 0 14 14"><path d="M7 1v12M1 7h12" stroke="#fff" stroke-width="2"/></svg></div><div class="vw">View</div></div>

<div class="gcard" style="left:-187px;top:3189px"><div class="gimg" role="img" aria-label="White portable concentrator" style="background:linear-gradient(90deg,#cfd8e0,#f2f4f6)"></div></div>
<div class="gcard" style="left:133px;top:3189px"><div class="plus"><svg width="14" height="14" viewBox="0 0 14 14"><path d="M7 1v12M1 7h12" stroke="#fff" stroke-width="2"/></svg></div><div class="vw">View</div><div class="gimg" role="img" aria-label="Dark grey wheeled portable concentrator" style="background:linear-gradient(90deg,#6b6b6b,#2b2b2b)"></div></div>
<div class="gcard" style="left:455px;top:3189px"><div class="plus"><svg width="14" height="14" viewBox="0 0 14 14"><path d="M7 1v12M1 7h12" stroke="#fff" stroke-width="2"/></svg></div><div class="vw">View</div><div class="gimg" role="img" aria-label="White portable oxygen concentrator" style="background:linear-gradient(90deg,#f3f5f7,#c3d0dc)"></div></div>
<div class="gcard" style="left:775px;top:3189px"><div class="plus"><svg width="14" height="14" viewBox="0 0 14 14"><path d="M7 1v12M1 7h12" stroke="#fff" stroke-width="2"/></svg></div><div class="vw">View</div><div class="gimg" role="img" aria-label="Black oxygen concentrator on wheels" style="background:linear-gradient(90deg,#444,#151515)"></div></div>
<div class="gcard" style="left:1095px;top:3189px"><div class="plus"><svg width="14" height="14" viewBox="0 0 14 14"><path d="M7 1v12M1 7h12" stroke="#fff" stroke-width="2"/></svg></div><div class="vw">View</div></div>

<div class="dots" style="left:563px;top:3394px"><i></i><i></i><i></i></div>

<!-- contact -->
<section class="contact">
  <div class="eb">How can we help you?</div>
  <h2>LEAVE US A MESSAGE</h2>
  <div class="crow" style="top:154px">
    <svg width="26" height="26" viewBox="0 0 26 26"><circle cx="13" cy="8" r="5" fill="none" stroke="var(--blue)" stroke-width="1.6"/><path d="M3 24a10 10 0 0 1 20 0" fill="none" stroke="var(--blue)" stroke-width="1.6"/></svg>
    <span class="t">Contact With a form for connect with us</span><a class="btn btn-blue">SUBMIT A FORM</a>
  </div>
  <div class="hr" style="top:230px"></div>
  <div class="crow" style="top:248px">
    <svg width="26" height="26" viewBox="0 0 26 26"><rect x="4" y="2" width="16" height="22" rx="2" fill="none" stroke="var(--blue)" stroke-width="1.6"/><path d="M8 8h8M8 12h8M8 16h5" stroke="var(--blue)" stroke-width="1.6"/></svg>
    <span class="t">Get a personalized quote tailored</span><a class="btn btn-outline">REQUESTA QUOTE</a>
  </div>
  <div class="hr" style="top:322px"></div>
  <div class="crow" style="top:340px">
    <svg width="26" height="26" viewBox="0 0 26 26"><path d="M5 2h11l5 5v17H5z" fill="none" stroke="var(--blue)" stroke-width="1.6"/><path d="M9 13h8M9 17h8" stroke="var(--blue)" stroke-width="1.6"/></svg>
    <span class="t">Contact inquiries, support, collaboration</span><a class="btn btn-outline-blue">GET IN TOUCH</a>
  </div>
  <div class="photo" role="img" aria-label="Support agent wearing a headset"></div>
</section>

<!-- brands -->
<div class="eyebrow" style="top:4023px">All Manufacturers</div>
<h2 class="sec-title" style="top:4058px">SHOP BY BRAND</h2>
<div class="brandbox" style="left:106px">CALVORA</div>
<div class="brandbox" style="left:218px">Invexa</div>
<div class="brandbox" style="left:330px">Krevan</div>
<div class="brandbox" style="left:442px">Gelmont</div>
<div class="brandbox" style="left:554px">brevix</div>
<div class="brandbox" style="left:666px">aerivo</div>
<div class="brandbox" style="left:778px">dravo</div>
<div class="brandbox" style="left:890px">VARNOTH<br>RESPIRA</div>
<div class="brandbox" style="left:1002px">TORVELL<br>LABS</div>
<div class="dots" style="left:568px;top:4234px"><i></i><i></i><i></i></div>

<!-- most viewed -->
<div class="eyebrow" style="top:4307px">Featured Products</div>
<h2 class="sec-title" style="top:4341px">MOST VIEWED PRODUCTS</h2>
<a class="view-all" style="left:896px;top:4343px">Recently Viewed <svg width="16" height="12" viewBox="0 0 16 12"><path d="M1 6h13M9 1l5 5-5 5" fill="none" stroke="#444" stroke-width="1.5"/></svg></a>

<div class="pcard" style="left:-108px;top:4407px"><div class="pimg" role="img" aria-label="Blue home oxygen concentrator" style="background:linear-gradient(90deg,#2f7fc9,#5fa8e6)"></div><div class="bl">Pulmatek</div><div class="nm">Lumen 5 Pro</div><div class="lbl">BRANDS</div><div class="brs">Varnoth | Torvell Labs Inc</div></div>
<div class="pcard" style="left:133px;top:4407px"><div class="pimg" role="img" aria-label="Blue stationary oxygen concentrator" style="background:linear-gradient(90deg,#3b8fd6,#7bb9ea)"></div><div class="bl">Varnoth Healthcare</div><div class="nm">Varnoth Calmflo</div><div class="lbl">BRANDS</div><div class="brs">AERIVO BV &nbsp;|&nbsp; Varnoth Healthcare &nbsp;|&nbsp; Torvell Labs Inc</div></div>
<div class="pcard" style="left:374px;top:4407px"><div class="pimg" role="img" aria-label="Grey and black oxygen concentrator" style="background:linear-gradient(90deg,#9a9a9a,#dcdcdc 50%,#3a3a3a)"></div><div class="bl">Varnoth Healthcare</div><div class="nm">Varnoth Airmate</div><div class="lbl">BRANDS</div><div class="brs">Varnoth Healthcare &nbsp;|&nbsp; Torvell Labs Inc</div></div>
<div class="pcard" style="left:616px;top:4407px"><div class="pimg" role="img" aria-label="White portable oxygen concentrator" style="background:linear-gradient(90deg,#e8eef3,#c5d3de)"></div><div class="bl">Brevix</div><div class="nm">Brevix Roam 6</div><div class="lbl">BRANDS</div><div class="brs">Brevix</div></div>
<div class="pcard" style="left:856px;top:4407px"><div class="pimg" role="img" aria-label="White and blue compact oxygen concentrator" style="background:linear-gradient(90deg,#dfe9f2,#9fbedb)"></div><div class="bl">Pulmatek</div><div class="nm">Lumen 5</div><div class="lbl">BRANDS</div><div class="brs">Pulmatek</div></div>
<div class="pcard" style="left:1097px;top:4407px"><div class="pimg" role="img" aria-label="White and blue compact oxygen concentrator" style="background:linear-gradient(90deg,#dfe9f2,#9fbedb)"></div><div class="bl">Pulmatek</div><div class="nm">Lumen 5</div><div class="lbl">BRANDS</div><div class="brs">Pulmatek</div></div>
<div class="car-arrow" style="left:102px;top:4526px"><svg width="14" height="14" viewBox="0 0 14 14"><path d="M9 2L4 7l5 5" fill="none" stroke="#fff" stroke-width="1.8"/></svg></div>
<div class="car-arrow" style="left:1052px;top:4526px"><svg width="14" height="14" viewBox="0 0 14 14"><path d="M5 2l5 5-5 5" fill="none" stroke="#fff" stroke-width="1.8"/></svg></div>

<!-- footer -->
<footer class="footer">
  <div class="col" style="left:133px"><h5>ABOUT US</h5><ul><li>About Us</li><li>Delivery</li><li>Privacy Policy</li><li>Terms &amp; Conditions</li><li>Business</li></ul></div>
  <div class="col" style="left:378px"><h5>CUSTOMER SERVICE</h5><ul><li>Contact</li><li>Warranty and Service</li><li>Returns</li><li>Site Map</li><li>Brands</li></ul></div>
  <div class="col" style="left:618px"><h5>MY ACCOUNT</h5><ul><li>My Account</li><li>Order History</li></ul></div>
  <div class="col" style="left:860px"><h5>DOCUMENTATION</h5><ul><li>FAQ</li></ul></div>
  <div class="bottom">Copyright 2025 GP luchtvoorraadpunt &nbsp;All Rights Reserved</div>
</footer>
<div class="video-btn" aria-label="Video channel">Video</div>
<div class="up-btn"><svg width="18" height="22" viewBox="0 0 18 22"><path d="M9 21V2M2 9l7-7 7 7" fill="none" stroke="#fff" stroke-width="2"/></svg></div>

</body>
</html>
```